Redesign Of Current Landing Page

I need to redesign this landing page https://www.brightlanepromo.biz/?page=landing&landing=23 (Please do not opt in because when you do it will show you the home page. Please clear your cookies before going to this url above to view the 1 page landing page.)

Please use my updated website as a reference for colors and logo.
http://sitecradlewerk.com/dh/bpq/index.html

I would like the call to action to be a button that opens into a lead form...

Button would be "Download Samples"

Target Market(s)

small business owners

Industry/Entity Type

Marketing

Number of Pages Required

1 page

Colors

Designer to choose colors to be used in the design.

Requirements
Must have
• must be full responsive on all devices
Nice to have
• must have a legitimate professional apeal to it
Should not have
• open

```html
<!DOCTYPE html>
<html lang="en">
<head>
<meta charset="utf-8">
<title>Bright Lane Promo – Attract More Customers</title>
<link href="https://fonts.googleapis.com/css2?family=Nunito:wght@400;700;800&family=Open+Sans:wght@300;400;600&display=swap" rel="stylesheet">
<style>
:root{
  --brand:#2b7fae;
  --ink:#333333;
  --muted:#666666;
  --line:#d9d9d9;
  --white:#ffffff;
}
*{box-sizing:border-box;margin:0;padding:0}
html,body{width:1200px;height:2350px;overflow:hidden}
body{font-family:"Open Sans",Arial,sans-serif;color:var(--ink);background:var(--white);position:relative}
.abs{position:absolute}

.top-rule{left:0;top:0;width:1200px;height:6px;background:var(--brand)}
.site-header{left:0;top:6px;width:1200px;height:113px}
.brand-name{font-family:"Open Sans",Arial,sans-serif;font-weight:600;font-size:24px;color:var(--ink);white-space:nowrap}
.header-brand{left:90px;top:44px}
.btn-download{left:925px;top:38px;width:186px;height:39px;border-radius:20px;background:var(--brand);color:var(--white);font-size:15px;display:flex;align-items:center;justify-content:center}

.hero{left:0;top:119px;width:1200px;height:468px;background:linear-gradient(180deg,#2a2f36 0%,#1b1f25 55%,#111317 100%)}
.hero-title{left:90px;top:165px;font-family:"Nunito",Arial,sans-serif;color:var(--white)}
.hero-title strong{display:block;font-size:31px;font-weight:800;letter-spacing:.3px}
.hero-title span{display:block;font-size:27px;font-weight:400;line-height:38px;margin-top:2px}
.hero-arrows{left:92px;top:298px;display:flex;gap:8px}
.hero-arrow{width:28px;height:28px;border:1.5px solid var(--white);border-radius:50%;display:flex;align-items:center;justify-content:center}
.hero-cards{left:715px;top:56px;width:362px;height:332px;background:linear-gradient(135deg,#3b6fb8 0%,#c0392b 40%,#1d7a45 70%,#6b2f8a 100%);opacity:.85;border-radius:4px}

.imagine{left:0;top:587px;width:1200px;height:280px;text-align:center}
.imagine h2{margin-top:64px;font-size:26px;font-weight:400;color:#2b2b2b}
.imagine p{width:870px;margin:16px auto 0;font-size:12.5px;line-height:23px;color:var(--muted);text-align:justify;text-align-last:center}

.why{left:0;top:867px;width:1200px;height:438px;background:linear-gradient(90deg,#f4f5f7 0%,#eceef1 60%,#f2f3f5 100%)}
.why h2{position:absolute;top:80px;width:100%;text-align:center;font-size:30px;font-weight:400;color:#2b2b2b}
.benefit{top:175px;width:260px;text-align:center}
.benefit-icon{width:106px;height:106px;border-radius:50%;background:var(--brand);border:3px solid #9fc3db;margin:0 auto;display:flex;align-items:center;justify-content:center}
.benefit p{margin-top:28px;font-size:16px;line-height:24px;color:#444;text-transform:uppercase}

.how{left:0;top:1305px;width:1200px;height:419px}
.video{left:100px;top:73px;width:402px;height:280px;background:linear-gradient(135deg,#dfe6ee 0%,#b9c6d3 50%,#eef1f4 100%);box-shadow:0 0 0 4px #f1f1f1,0 2px 6px rgba(0,0,0,.2);display:flex;align-items:center;justify-content:center}
.how-copy{left:550px;top:86px;width:545px}
.how-copy h2{font-size:30px;font-weight:400;letter-spacing:.5px;color:#2b2b2b}
.how-copy p{margin-top:10px;font-size:12.5px;line-height:22px;color:var(--muted);text-align:justify}
.how-copy p+p{margin-top:0}
.btn-more{display:inline-block;margin-top:12px;padding:6px 14px;border:1.5px solid var(--brand);border-radius:16px;font-size:11px;color:var(--brand)}

.testimonial{left:0;top:1724px;width:1200px;height:301px;background:var(--brand)}
.portrait{left:133px;top:74px;width:164px;height:164px;border-radius:50%;background:linear-gradient(180deg,#dfe4ea 0%,#8794a3 60%,#2f3a4a 100%);border:3px solid #d6e6f1}
.quote-badge{left:132px;top:75px;width:46px;height:46px;border-radius:50%;background:#27a0dc;border:3px solid var(--white);color:var(--white);font-family:Georgia,serif;font-size:34px;line-height:48px;text-align:center}
.quote{left:318px;top:88px;width:770px;color:var(--white)}
.quote p{font-size:14.5px;line-height:25px}
.quote cite{display:block;margin-top:12px;margin-left:4px;font-style:normal;font-size:14.5px;line-height:24px}

.site-footer{left:0;top:2025px;width:1200px;height:325px}
.footer-brand{left:90px;top:134px}
.footer-col{top:80px}
.footer-col h3{font-size:15px;font-weight:400;color:#333;text-transform:uppercase;margin-bottom:14px}
.footer-col p{font-size:12px;line-height:22px;color:#777}
.signup{display:flex;margin-top:12px}
.signup-field{width:147px;height:32px;border:1px solid #ccc;font-size:12px;color:#888;padding:7px 8px}
.signup-btn{height:32px;padding:0 9px;background:var(--brand);color:var(--white);font-size:12px;display:flex;align-items:center}
.social{display:flex;gap:14px;margin-top:6px}
.social span{width:24px;height:24px;border-radius:4px;background:#555}
.footer-rule{left:88px;top:250px;width:1024px;height:1px;background:var(--line)}
.copyright{left:0;top:280px;width:1200px;text-align:center;font-size:12px;color:#333}
</style>
</head>
<body>
<div class="abs top-rule"></div>

<header class="abs site-header">
  <div class="abs brand-name header-brand">Bright Lane Promo</div>
  <div class="abs btn-download">Download Samples</div>
</header>

<section class="abs hero" role="img" aria-label="Night-time city skyline viewed from above">
  <h1 class="abs hero-title"><strong>ATTRACT MORE CUSTOMERS</strong><span>who spend more money with your<br>business more often!</span></h1>
  <div class="abs hero-arrows">
    <span class="hero-arrow"><svg width="10" height="10" viewBox="0 0 10 10"><path d="M6.5 1.5 3 5l3.5 3.5" fill="none" stroke="#fff" stroke-width="1.6"/></svg></span>
    <span class="hero-arrow"><svg width="10" height="10" viewBox="0 0 10 10"><path d="M3.5 1.5 7 5 3.5 8.5" fill="none" stroke="#fff" stroke-width="1.6"/></svg></span>
  </div>
  <div class="abs hero-cards" role="img" aria-label="Fanned stack of printed incentive certificates for travel, cash back and electronics"></div>
</section>

<section class="abs imagine">
  <h2>IMAGINE</h2>
  <p>being able to create exciting give away promotions that will boost your sales without ever having to worry about cost. Bright Lane Promo Group, Inc. provides high-perceived value promotional incentives to businesses that want to advertise an exciting Give Away that will instantly attract more customers from your existing advertising efforts. Your business can give away incentive certificates that are redeemable for luxury hotel &amp; resort stays with airfare included, cruises, cash for gas, groceries, dining and even electronic goods.</p>
</section>

<section class="abs why">
  <h2>WHY OFFER INCENTIVES TO CUSTOMERS?</h2>
  <div class="abs benefit" style="left:73px">
    <div class="benefit-icon"><svg width="40" height="34" viewBox="0 0 40 34" fill="#fff"><rect x="2" y="30" width="36" height="3"/><rect x="2" y="4" width="3" height="29"/><rect x="9" y="18" width="5" height="10"/><rect x="17" y="12" width="5" height="16"/><rect x="25" y="15" width="5" height="13"/><rect x="32" y="8" width="4" height="20"/></svg></div>
    <p>Increase responses<br>from your existing ads</p>
  </div>
  <div class="abs benefit" style="left:340px">
    <div class="benefit-icon"><svg width="38" height="38" viewBox="0 0 38 38"><path d="M29 4a8 8 0 0 0-9 10L5 29a3 3 0 0 0 4 4l15-15a8 8 0 0 0 10-9l-5 5-5-1-1-5z" fill="#fff"/></svg></div>
    <p>#1 sales closing tool<br>- gift w/ purchase</p>
  </div>
  <div class="abs benefit" style="left:610px">
    <div class="benefit-icon"><svg width="38" height="36" viewBox="0 0 38 36"><path d="M19 1l5.3 11.3 12.2 1.5-9 8.4 2.4 12.1L19 28.3 8.1 34.3l2.4-12.1-9-8.4 12.2-1.5z" fill="#fff"/></svg></div>
    <p>Build brand<br>awareness and trust</p>
  </div>
  <div class="abs benefit" style="left:876px">
    <div class="benefit-icon"><svg width="44" height="34" viewBox="0 0 44 34" fill="#fff"><circle cx="22" cy="9" r="6"/><circle cx="9" cy="11" r="4.5"/><circle cx="35" cy="11" r="4.5"/><path d="M12 32c0-8 4-13 10-13s10 5 10 13z"/><path d="M1 28c0-6 3-10 8-10 2 0 3 .5 4 1.5-2 2.5-3 5-3 8.5z"/><path d="M43 28c0-6-3-10-8-10-2 0-3 .5-4 1.5 2 2.5 3 5 3 8.5z"/></svg></div>
    <p>Insure the sale over<br>your competition</p>
  </div>
</section>

<section class="abs how">
  <div class="abs video" role="img" aria-label="Video still of a person working at a laptop on a desk">
    <svg width="60" height="60" viewBox="0 0 60 60"><circle cx="30" cy="30" r="28" fill="rgba(40,40,40,.55)"/><path d="M24 18l18 12-18 12z" fill="#fff"/></svg>
  </div>
  <div class="abs how-copy">
    <h2>HOW CAN WE DO IT?</h2>
    <p>We help fill empty rooms for thousands of hotels and resorts in hundreds of destinations around the world as well as the major cruise lines. Hotels and resorts are rarely full so when we place someone in their empty rooms, they end up making it up when travelers spend money on room service, spa services, eat at their in-house restaurants, casino and take advantage of other amenities that drive revenue.</p>
    <p>We also help over 18,000 restaurants, electronic manufacturers, the major gas companies and top grocery chains in the U.S and Canada increase brand awareness as well as increase customer loyalty.</p>
    <span class="btn-more">READ MORE</span>
  </div>
</section>

<section class="abs testimonial">
  <div class="abs portrait" role="img" aria-label="Portrait photo of the customer giving the testimonial"></div>
  <div class="abs quote-badge">&ldquo;</div>
  <blockquote class="abs quote">
    <p>I began using your incentives two years ago to boost lead generation efforts. I have experienced a 63% increase in lead captures. And, even more importantly, my sales have increased as well. The ability to offer unlimited certificates and not having to pay for each certificate I give away is perhaps the best feature of the program, but having the flexibility to email or print certificates for my customers is also won-</p>
    <cite>Sam R.<br>Brookdale, TN</cite>
  </blockquote>
</section>

<footer class="abs site-footer">
  <div class="abs brand-name footer-brand">Bright Lane Promo</div>
  <div class="abs footer-col" style="left:340px">
    <h3>Contact Us</h3>
    <p>Address : 12 Hollin Lane, Eastfield<br>Leeds, LS9 4QT<br>Phone : 07400 555 019<br>Email : info@brightlanepromo.biz</p>
  </div>
  <div class="abs footer-col" style="left:661px">
    <h3>Join Our Mailing List</h3>
    <p>Your about us information would fit<br>here nicely.</p>
    <div class="signup"><span class="signup-field">Email address</span><span class="signup-btn">Submit</span></div>
  </div>
  <div class="abs footer-col" style="left:935px">
    <h3>Follow Us Out There</h3>
    <div class="social"><span></span><span></span><span></span><span></span></div>
  </div>
  <div class="abs footer-rule"></div>
  <p class="abs copyright">Copyright © 2017. All Rights Reserved</p>
</footer>
</body>
</html>
```